Harrow Grading LLC business card design

Excavation company business cards

Contact Information for Business Card

Harrow Grading LLC cell phone 208-417-6290 office phone 208-319-4856 harrowgradingllc@maplecove.com Driveways, site prep, retaining walls, septic systems, rock delivery

Colors

Designer to choose colors to be used in the design.

```html
<!DOCTYPE html>
<html lang="en">
<head>
<meta charset="utf-8">
<title>Harrow Grading LLC business card</title>
<link href="https://fonts.googleapis.com/css2?family=Montserrat:wght@400;700;800&display=swap" rel="stylesheet">
<style>
  :root {
    --page: #e9e7e4;
    --card-white: #ffffff;
    --card-black: #1b1b1c;
    --black-mark: #2a2a2b;
    --orange: #ec6f24;
    --ink: #4a4a4a;
    --white: #ffffff;
  }
  * { box-sizing: border-box; margin: 0; padding: 0; }
  html, body { width: 1200px; height: 912px; overflow: hidden; }
  body {
    background: var(--page);
    font-family: "Montserrat", sans-serif;
    display: flex;
    flex-direction: column;
    align-items: center;
    justify-content: center;
    gap: 32px;
  }
  .card {
    width: 700px;
    height: 400px;
    position: relative;
    box-shadow: 0 6px 18px rgba(0,0,0,0.18);
  }
  /* back side */
  .card-back {
    background: var(--card-black);
    display: flex;
    align-items: center;
    justify-content: center;
  }
  .card-back .brand-name {
    color: var(--black-mark);
    font-weight: 800;
    font-size: 46px;
    letter-spacing: 1px;
    text-transform: uppercase;
    display: flex;
    align-items: center;
    gap: 18px;
  }
  .brand-square {
    width: 34px; height: 34px;
    background: currentColor;
    display: inline-block;
  }
  /* front side */
  .card-front { background: var(--card-white); }
  .front-brand {
    position: absolute;
    top: 78px;
    left: 0; right: 0;
    display: flex;
    justify-content: center;
    align-items: center;
    gap: 14px;
    color: var(--orange);
    font-weight: 800;
    font-size: 36px;
    text-transform: uppercase;
    letter-spacing: 1px;
  }
  .front-brand .brand-square { width: 28px; height: 28px; }
  .info-band {
    position: absolute;
    top: 218px;
    left: 0; right: 0;
    height: 92px;
    background: var(--orange);
    color: var(--white);
    display: flex;
    align-items: center;
  }
  .person {
    width: 330px;
    text-align: right;
    padding-right: 26px;
  }
  .person-name {
    font-weight: 700;
    font-size: 24px;
    text-transform: uppercase;
    letter-spacing: 0.5px;
  }
  .person-role { font-size: 18px; margin-top: 2px; }
  .divider { width: 2px; height: 62px; background: var(--white); }
  .contacts {
    list-style: none;
    padding-left: 22px;
    font-size: 16px;
    line-height: 1.3;
  }
  .contacts li { display: flex; align-items: center; gap: 8px; }
  .contacts svg { width: 12px; height: 12px; fill: none; stroke: var(--white); stroke-width: 1.6; }
  .services {
    position: absolute;
    top: 334px;
    left: 0; right: 0;
    text-align: center;
    font-size: 17px;
    color: var(--ink);
  }
  .services .sep { color: var(--orange); margin: 0 4px; }
</style>
</head>
<body>
  <section class="card card-back" aria-label="Card back">
    <div class="brand-name"><span class="brand-square"></span>Harrow Grading LLC</div>
  </section>

  <section class="card card-front" aria-label="Card front">
    <div class="front-brand"><span class="brand-square"></span>Harrow Grading LLC</div>

    <div class="info-band">
      <div class="person">
        <p class="person-name">Dale Whitford</p>
        <p class="person-role">Director</p>
      </div>
      <div class="divider"></div>
      <ul class="contacts">
        <li><svg viewBox="0 0 12 12"><rect x="3" y="0.8" width="6" height="10.4" rx="1"/></svg>208-417-6290</li>
        <li><svg viewBox="0 0 12 12"><path d="M1 4 Q6 0 11 4 L9 6 L8 4.5 L4 4.5 L3 6 Z M2.5 7 H9.5 V11 H2.5 Z"/></svg>208-319-4856</li>
        <li><svg viewBox="0 0 12 12"><rect x="0.8" y="2.5" width="10.4" height="7" rx="0.6"/><path d="M0.8 2.5 L6 6.5 L11.2 2.5"/></svg>harrowgradingllc@maplecove.com</li>
      </ul>
    </div>

    <p class="services">Driveways,<span class="sep">|</span>site prep,<span class="sep">|</span>retaining walls,<span class="sep">|</span>septic systems,<span class="sep">|</span>rock delivery</p>
  </section>
</body>
</html>
```